Business cards to launch an education platform

Hi,
I am looking at having new business cards designed.
I am a startup, developing a web platform for schools and university, the education world. It's an online assessment system.
I would like a card that looks classy, and that is using the colors and the font of my logo.

I have attached:
1) my logo
2) A business card that I have designed quickly so you can have all the information required in the card, but I really don't like it.
3) The font that I am using (Lato Regular) to design my web platform
4) Some screenshots of my web platform so you can have a look at the style that I have.

Target Market(s)

Major market: Education system: Schools and university
Minor markets: Business in general

Industry/Entity Type

Business

Contact Information for Business Card

Clara Fenwick
Director

M: 0437 518 902
E: clara.fenwick@amberLoomSystems.com.au

Requirements
Must have
• The colors of my logo

```html
<!DOCTYPE html>
<html lang="en">
<head>
<meta charset="utf-8">
<title>Amber Loom Systems – Business Card</title>
<link href="https://fonts.googleapis.com/css2?family=Lato:wght@400;700&display=swap" rel="stylesheet">
<style>
  :root {
    --page-bg: #e9ebee;
    --blue-deep: #0a5f9e;
    --blue-main: #1479bd;
    --blue-light: #2aa0d8;
    --cyan: #35b6e3;
    --card-white: #ffffff;
    --text-blue: #1a6fae;
  }
  * { margin: 0; padding: 0; box-sizing: border-box; }
  html, body {
    width: 1200px;
    height: 780px;
    overflow: hidden;
    background: var(--page-bg);
    font-family: "Lato", sans-serif;
  }
  .business-card {
    position: absolute;
    left: 100px;
    top: 105px;
    width: 1000px;
    height: 570px;
    border-radius: 4px;
    overflow: hidden;
    box-shadow: 0 14px 36px rgba(10, 60, 100, 0.22);
  }
  .card-art {
    position: absolute;
    inset: 0;
    width: 100%;
    height: 100%;
  }
  .brand {
    position: absolute;
    top: 88px;
    right: 210px;
    display: flex;
    align-items: center;
    gap: 16px;
  }
  .brand-square {
    width: 34px;
    height: 34px;
    background: var(--blue-main);
  }
  .brand-name {
    font-weight: 400;
    font-size: 34px;
    letter-spacing: 3px;
    color: var(--blue-main);
  }
  .contact-block {
    position: absolute;
    left: 250px;
    bottom: 84px;
  }
  .person-name {
    font-weight: 700;
    font-size: 34px;
    color: var(--text-blue);
    line-height: 1.05;
  }
  .person-role {
    font-weight: 400;
    font-size: 24px;
    color: var(--cyan);
    margin-bottom: 26px;
  }
  .contact-line {
    display: flex;
    align-items: center;
    gap: 14px;
    font-size: 22px;
    color: var(--text-blue);
    margin-top: 10px;
  }
  .contact-icon {
    width: 28px;
    height: 28px;
    flex: none;
  }
</style>
</head>
<body>
  <section class="business-card">
    <svg class="card-art" viewBox="0 0 1000 570" aria-hidden="true">
      <defs>
        <linearGradient id="bandBlue" x1="0" y1="0" x2="1" y2="1">
          <stop offset="0" stop-color="#2aa0d8"/>
          <stop offset="0.5" stop-color="#1479bd"/>
          <stop offset="1" stop-color="#0a5f9e"/>
        </linearGradient>
      </defs>
      <rect width="1000" height="570" fill="url(#bandBlue)"/>
      <path d="M150 0 H830 Q930 285 850 570 H200 Q70 285 150 0 Z" fill="#ffffff"/>
    </svg>

    <div class="brand">
      <span class="brand-square"></span>
      <span class="brand-name">AMBER LOOM SYSTEMS</span>
    </div>

    <div class="contact-block">
      <p class="person-name">Clara Fenwick</p>
      <p class="person-role">Director</p>
      <p class="contact-line">
        <svg class="contact-icon" viewBox="0 0 28 28" aria-label="Phone">
          <rect width="28" height="28" rx="3" fill="#35b6e3"/>
          <rect x="9" y="5" width="10" height="18" rx="2" fill="none" stroke="#fff" stroke-width="2"/>
          <circle cx="14" cy="19.5" r="1.2" fill="#fff"/>
        </svg>
        0437 518 902
      </p>
      <p class="contact-line">
        <svg class="contact-icon" viewBox="0 0 28 28" aria-label="Email">
          <rect width="28" height="28" rx="3" fill="#35b6e3"/>
          <rect x="6" y="8" width="16" height="12" fill="none" stroke="#fff" stroke-width="2"/>
          <path d="M6 8 L14 15 L22 8" fill="none" stroke="#fff" stroke-width="2"/>
        </svg>
        clara.fenwick@amberLoomSystems.com.au
      </p>
    </div>
  </section>
</body>
</html>
```